Website Design for a Chemical Sales Company

We are working with a Chemical Sales Company in California. They sell various chemicals throughout the US.
Types of products they sell: https://www.wardenvale.example/us/products/all
https://www.molvista.example/products/kerrin/glacyn-glycol-thermal-fluids/glacyn-propylene-glycol-thermal-fluids
Some sites to use for inspiration:
https://www.molvista.example
https://www.kerrin.example/en-us
Thank you for taking the time to consider designing a website for us. We are web developers based in Stockton, CA, USA. Most of our projects go through the same process. Understanding this process may help you win a project with us. We custom-code all of our websites in-house. We don’t have any requirements as to what tools you use for your design, but we ask that you follow these guidelines.
IMAGES:
If you use any images or icons in the design, we ask that you have a link to the asset so we can purchase the image/icon. Most of the designs we submit do not have the customer’s images on them unless they have some great images. Be creative; show us the feeling you are trying to portray with your image choices. Use any royalty-free site you choose. We subscribe to Pelmora and mainly use their images, but we can purchase images outside of Pelmora. PLEASE NOTE: we will not submit designs to clients with watermarks on the images.
FONTS:
We ask that you identify the fonts you’re using in the design. This can be done in a message if you want. We typically use Google Fonts and Pelmora Fonts.
CONTENT:
We're always open to different content and ideas. We often submit designs with stock images so the client can see our vision. We typically take pictures after the website launch to use their images with our vision. Lorem Ipsum is fine for paragraphs, but we ask that you make the Headers with correct English. We want to be able to show the vision and identify the sections of the website.
INSPIRATION:
We typically add a couple of links in the brief of websites we like to help you get started in your design.
REVISIONS:
We do not often ask for revisions of the designs unless we see something in the design that may not appeal to the client. If there are slight changes that we want to make, we do that in the development process.
FEEDBACK:
We rarely give feedback on designs during the design process. We are working on many website projects and do not have the time to provide feedback. We usually respond if your request is well thought out and asks specific questions, but a note asking “feedback, please” usually goes unanswered.

```html
<!DOCTYPE html>
<html lang="en">
<head>
<meta charset="utf-8">
<title>Ionvale — Chemical Sales</title>
<link rel="stylesheet" href="https://fonts.googleapis.com/css2?family=Lexend:wght@300;400;500&family=Poppins:wght@400;500&display=swap">
<style>
:root{
  --blue:#0a8fe0;
  --blue-deep:#0062c9;
  --blue-light:#46b3f0;
  --ink:#1a1a1a;
  --text:#2a2a2a;
  --muted:#9aa3ab;
  --white:#ffffff;
  --dark:#03080f;
  --star:#f5a623;
}
*{margin:0;padding:0;box-sizing:border-box}
html,body{width:1200px;height:4438px;overflow:hidden;background:var(--white)}
body{position:relative;font-family:"Poppins",sans-serif;color:var(--text)}
.abs{position:absolute}
.heading{font-family:"Lexend",sans-serif;font-weight:300;color:var(--blue);letter-spacing:1px;text-transform:uppercase}
.brand{font-family:"Lexend",sans-serif;font-weight:300;letter-spacing:3px;display:flex;align-items:center;gap:12px}
.brand .dot{width:14px;height:14px;border-radius:50%;background:var(--blue)}
.btn{font-family:"Lexend",sans-serif;font-weight:400;color:var(--white);background:var(--blue);border-radius:10px;display:flex;align-items:center;justify-content:center;text-transform:uppercase}

/* header */
.topbar{left:420px;top:0;width:780px;height:60px;background:var(--blue);display:flex;align-items:center;padding-left:58px;gap:28px;color:var(--white);font-family:"Lexend",sans-serif;font-size:15px;clip-path:polygon(28px 0,100% 0,100% 100%,0 100%)}
.topbar .item{display:flex;align-items:center;gap:14px}
.ring{width:36px;height:36px;border:2px solid var(--white);border-radius:50%;display:flex;align-items:center;justify-content:center}
.nav{top:88px;left:492px;display:flex;gap:40px;font-family:"Lexend",sans-serif;font-size:14px;color:var(--ink)}

/* about */
.about{left:600px;top:898px;width:490px;display:flex;flex-direction:column;align-items:flex-start}
.about p{margin-top:22px;font-size:15.5px;line-height:36px;text-align:justify}
.about .btn{margin-top:28px;width:207px;height:56px;font-size:25px;box-shadow:6px 6px 0 #c9e3f6}

/* products */
.card{top:1632px;width:317px;height:453px;background:var(--white);border-radius:12px;text-align:center}
.card .shot{margin:28px auto 0;width:190px;height:180px;border-radius:8px}
.card h3{margin-top:38px;font-size:23px}
.card p{margin:12px 16px 0;font-size:16px;line-height:30px;text-align:justify}
.card a,.news a{display:inline-block;margin-top:22px;font-family:"Lexend",sans-serif;font-size:20px;color:var(--blue);text-decoration:underline}
.arrow{width:46px;height:46px;border-radius:50%;background:var(--white);display:flex;align-items:center;justify-content:center}

/* partners */
.partner{top:2985px;width:188px;height:176px;background:var(--white);border-radius:6px;display:flex;align-items:center;justify-content:center}
.partner span{width:70px;height:70px;border-radius:50%;background:#d6ebfa}

/* news */
.news{background:var(--white);border:3px solid #e5e5e5;border-radius:10px}
.news .date{font-family:"Lexend",sans-serif;color:var(--blue);font-size:18px}
.news p{font-size:16px;line-height:31px;text-align:justify;margin-top:8px}
.news a{margin-top:6px}
.news .thumb{flex:0 0 203px;margin:7px;width:203px;height:225px}
</style>
</head>
<body>

<!-- header -->
<div class="abs brand" style="left:110px;top:52px;font-size:32px;color:#333"><span class="dot"></span>IONVALE</div>
<div class="abs topbar">
  <div class="item"><span class="ring"><svg width="16" height="16" viewBox="0 0 24 24" fill="#fff"><path d="M6.6 10.8a15.1 15.1 0 006.6 6.6l2.2-2.2a1 1 0 011-.25 11.4 11.4 0 003.6.57 1 1 0 011 1V20a1 1 0 01-1 1A17 17 0 013 4a1 1 0 011-1h3.5a1 1 0 011 1c0 1.25.2 2.45.57 3.57a1 1 0 01-.25 1z"/></svg></span>+1 555 010 2040</div>
  <div class="item" style="margin-left:28px"><span class="ring"><svg width="18" height="14" viewBox="0 0 24 18" fill="none" stroke="#fff" stroke-width="2"><rect x="1" y="1" width="22" height="16" rx="2"/><path d="M1 2l11 8 11-8"/></svg></span>HELLO@IONVALE.EXAMPLE</div>
  <div class="item" style="gap:10px"><span class="ring"></span><span class="ring"></span></div>
</div>
<nav class="abs nav"><span>HOME</span><span>ABOUT US</span><span>OUR PRODUCTS</span><span>LATEST NEWS</span><span>CONTACT US</span></nav>

<!-- hero -->
<svg class="abs" style="left:0;top:143px" width="1200" height="670" viewBox="0 0 1200 670">
  <defs>
    <linearGradient id="heroTone" x1="0" y1="0" x2="1" y2="1"><stop offset="0" stop-color="#dfeef8"/><stop offset=".55" stop-color="#8fc3e6"/><stop offset="1" stop-color="#2f7fc4"/></linearGradient>
    <clipPath id="heroClip"><path d="M0 0H1200V470C1000 620 640 680 380 650 180 625 40 570 0 520Z"/></clipPath>
  </defs>
  <g clip-path="url(#heroClip)"><rect width="1200" height="670" fill="url(#heroTone)" role="img" aria-label="Scientist in lab coat and cap looking through a microscope in a laboratory"/></g>
  <path d="M120 20C40 120 60 360 180 480 300 590 560 640 760 610 480 600 260 520 180 380 110 250 140 110 240 0Z" fill="#ffffff" opacity=".88"/>
</svg>
<div class="abs brand" style="left:215px;top:298px;font-size:58px;color:var(--ink)"><span class="dot" style="width:22px;height:22px"></span>IONVALE</div>
<p class="abs" style="left:212px;top:420px;width:470px;font-size:16px;line-height:40px">Sed ut perspiciatis unde omnis iste natus error sit voluptatem accusantium doloremque laudantium</p>
<div class="abs btn" style="left:333px;top:532px;width:209px;height:58px;font-size:24px">Get Started</div>

<!-- about -->
<svg class="abs" style="left:118px;top:895px" width="420" height="460" role="img" aria-label="Abstract glass atom orbit illustration"><defs><linearGradient id="orbit" x1="0" y1="0" x2="1" y2="1"><stop offset="0" stop-color="#e4f1fb"/><stop offset="1" stop-color="#6aa9dc"/></linearGradient></defs><ellipse cx="200" cy="230" rx="180" ry="200" fill="url(#orbit)" opacity=".55"/></svg>
<div class="abs about">
  <h2 class="heading" style="font-size:38px">About Us</h2>
  <p>Neque porro quisquam est, qui dolorem ipsum quia dolor sit amet, consectetur, adipisci velit, sed quia non numquam eius modi tempora incidunt ut labore et dolore magnam aliquam quaerat voluptatem. Ut enim ad minima veniam, quis nostrum exercitationem ullam corporis suscipit laboriosam, nisi ut aliquid ex ea commodi consequatur. Quis autem vel eum iure reprehenderit qui in ea voluptate velit esse quam nihil molestiae consequatur,</p>
  <div class="btn">Learn More</div>
</div>

<!-- products -->
<svg class="abs" style="left:0;top:1435px" width="1200" height="740"><defs><linearGradient id="prodBg" x1="0" y1="0" x2="1" y2="1"><stop offset="0" stop-color="#0a8fe0"/><stop offset="1" stop-color="#0062c9"/></linearGradient></defs><path d="M0 230C220 40 430 0 620 0 860 0 1080 90 1200 170V740H0Z" fill="url(#prodBg)"/></svg>
<h2 class="abs heading" style="left:0;width:1200px;top:1530px;text-align:center;color:var(--white);font-size:38px">Our Products</h2>
<div class="abs card" style="left:115px"><div class="shot" role="img" aria-label="Magnetic filter product photo" style="background:linear-gradient(#f2f2f2,#cfcfcf)"></div><h3 class="heading">Clearflow Separator</h3><p>Neque porro quisquam est, qui dolorem ipsum quia dolor sit amet, consectetur, adipisci velit,</p><a>VIEW DETAILS</a></div>
<div class="abs card" style="left:442px"><div class="shot" role="img" aria-label="Test kit case product photo" style="background:linear-gradient(#2a6fc4,#3aa35a)"></div><h3 class="heading">Rinsecheck Test Kit</h3><p>Neque porro quisquam est, qui dolorem ipsum quia dolor sit amet, consectetur, adipisci velit,</p><a>VIEW DETAILS</a></div>
<div class="abs card" style="left:767px"><div class="shot" role="img" aria-label="Inhibitor container product photo" style="background:linear-gradient(#f7e07a,#e8c22a)"></div><h3 class="heading">P200 Inhibitor</h3><p>Neque porro quisquam est, qui dolorem ipsum quia dolor sit amet, consectetur, adipisci velit,</p><a>VIEW DETAILS</a></div>
<div class="abs arrow" style="left:37px;top:1836px"><svg width="20" height="20" viewBox="0 0 20 20" fill="none" stroke="#0a8fe0" stroke-width="2.5"><path d="M16 10H4M9 5l-5 5 5 5"/></svg></div>
<div class="abs arrow" style="left:1113px;top:1836px"><svg width="20" height="20" viewBox="0 0 20 20" fill="none" stroke="#0a8fe0" stroke-width="2.5"><path d="M4 10h12M11 5l5 5-5 5"/></svg></div>

<!-- reviews -->
<h2 class="abs heading" style="left:0;width:1200px;top:2258px;text-align:center;font-size:38px">Customer Reviews</h2>
<div class="abs" style="left:-30px;top:2342px;width:115px;height:115px;border-radius:50%;background:#f1d9cc;opacity:.5" role="img" aria-label="Customer portrait"></div>
<div class="abs" style="left:1118px;top:2342px;width:115px;height:115px;border-radius:50%;background:#e9dfd7;opacity:.5" role="img" aria-label="Customer portrait"></div>
<div class="abs" style="left:543px;top:2342px;width:115px;height:115px;border-radius:50%;background:linear-gradient(#e6e6e6,#3a3a44)" role="img" aria-label="Customer portrait"></div>
<p class="abs" style="left:-30px;top:2490px;width:320px;font-size:15px;line-height:31px;color:var(--muted);text-align:right;opacity:.6">, qui dolorem ipsum quia dolor sit i velit, sed quia non numquam eius labore et dolore magnam aliquam</p>
<p class="abs" style="left:340px;top:2490px;width:520px;font-size:15px;line-height:31px;text-align:center">Neque porro quisquam est, qui dolorem ipsum quia dolor sit amet, consectetur, adipisci velit, sed quia non numquam eius modi tempora incidunt ut labore et dolore magnam aliquam</p>
<p class="abs" style="left:918px;top:2490px;width:320px;font-size:15px;line-height:31px;color:var(--muted);opacity:.6">Neque porro quisquam est, qui de amet, consectetur, adipisci velit, s modi tempora incidunt ut labore</p>
<div class="abs" style="left:0;width:1200px;top:2600px;text-align:center;color:var(--star);font-size:24px;letter-spacing:6px">★★★★★</div>
<div class="abs" style="left:-5px;top:2600px;color:var(--star);font-size:22px;letter-spacing:6px;opacity:.35">★★★</div>
<div class="abs" style="left:1110px;top:2600px;color:var(--star);font-size:22px;letter-spacing:6px;opacity:.35">★★★</div>
<div class="abs heading" style="left:0;width:1200px;top:2648px;text-align:center;font-size:21px;letter-spacing:0">- Lorem Lipsum</div>
<div class="abs" style="left:533px;top:2708px;display:flex;gap:14px"><span style="width:36px;height:6px;border-radius:3px;background:var(--blue)"></span><span style="width:36px;height:6px;border-radius:3px;background:#a9d4f2"></span><span style="width:36px;height:6px;border-radius:3px;background:#a9d4f2"></span></div>

<!-- partners -->
<div class="abs" style="left:0;top:2810px;width:1200px;height:440px;background:linear-gradient(135deg,var(--blue),var(--blue-deep))"></div>
<h2 class="abs heading" style="left:0;width:1200px;top:2883px;text-align:center;color:var(--white);font-size:38px">Proudly Partnered With</h2>
<div class="abs partner" style="left:112px"><span></span></div>
<div class="abs partner" style="left:308px"><span></span></div>
<div class="abs partner" style="left:504px"><span></span></div>
<div class="abs partner" style="left:700px"><span></span></div>
<div class="abs partner" style="left:897px"><span></span></div>
<div class="abs arrow" style="left:1108px;top:3200px;width:32px;height:32px"><svg width="14" height="14" viewBox="0 0 20 20" fill="none" stroke="#0a8fe0" stroke-width="3"><path d="M16 10H4M9 5l-5 5 5 5"/></svg></div>
<div class="abs arrow" style="left:1154px;top:3200px;width:32px;height:32px"><svg width="14" height="14" viewBox="0 0 20 20" fill="none" stroke="#0a8fe0" stroke-width="3"><path d="M4 10h12M11 5l5 5-5 5"/></svg></div>

<!-- news -->
<h2 class="abs heading" style="left:0;width:1200px;top:3333px;text-align:center;font-size:38px">Latest News</h2>
<div class="abs news" style="left:108px;top:3470px;width:428px;height:505px">
  <div role="img" aria-label="Gloved hand with pipette over test tubes" style="margin:7px;height:270px;background:linear-gradient(135deg,#5c97d2,#dbeaf7)"></div>
  <div style="padding:20px 22px 0 27px"><div class="date">15TH JUNE 2023</div><p>Neque porro quisquam est, qui dolorem ipsum quia dolor sit amet, consectetur, adipisci velit, sed quia non numquam eius</p><a>VIEW MORE</a></div>
</div>
<div class="abs news" style="left:548px;top:3465px;width:490px;height:245px;display:flex">
  <div class="thumb" role="img" aria-label="Modern laboratory interior" style="background:linear-gradient(135deg,#cfe3f3,#5d98c8)"></div>
  <div style="padding:25px 12px 0 20px"><div class="date">15TH JUNE 2023</div><p>Neque porro quisquam est, qui dolorem ipsum quia dolor sit amet, consectetur,</p><a>VIEW MORE</a></div>
</div>
<div class="abs news" style="left:548px;top:3728px;width:490px;height:245px;display:flex">
  <div class="thumb" role="img" aria-label="Glass flask on blue background" style="background:linear-gradient(135deg,#1b5ea8,#8bbde6)"></div>
  <div style="padding:25px 12px 0 20px"><div class="date">15TH JUNE 2023</div><p>Neque porro quisquam est, qui dolorem ipsum quia dolor sit amet, consectetur,</p><a>VIEW MORE</a></div>
</div>

<!-- footer -->
<svg class="abs" style="left:0;top:4040px" width="1200" height="398"><path d="M0 230C250 60 520 10 760 20 960 30 1110 80 1200 130V398H0Z" fill="#0a8fe0"/><path d="M0 260C250 90 520 40 760 48 960 58 1110 110 1200 160V398H0Z" fill="#03080f"/></svg>
<div class="abs brand" style="left:0;width:1200px;justify-content:center;top:4180px;font-size:34px;color:var(--white)"><span class="dot"></span>IONVALE</div>
<nav class="abs" style="left:0;width:1200px;top:4278px;display:flex;justify-content:center;gap:40px;font-family:'Lexend',sans-serif;font-size:15px;color:var(--white)"><span>HOME</span><span>ABOUT US</span><span>OUR PRODUCTS</span><span>LATEST NEWS</span><span>CONTACT US</span></nav>
<div class="abs" style="left:560px;top:4330px;display:flex;gap:12px"><span class="ring" style="width:34px;height:34px"></span><span class="ring" style="width:34px;height:34px"></span></div>
<div class="abs" style="left:0;width:1200px;top:4392px;text-align:center;font-family:'Lexend',sans-serif;font-size:14px;color:var(--white)">©2023 COPYRIGHTS. IONVALE. ALL RIGHTS RESERVED.</div>

</body>
</html>
```